Park furniture company needs a new product flyer

We're a street and park furniture supply company and we have a new range of furniture that we would like to showcase to prospective customers.
Pictures, logo and copy attached.
Furniture pictures are also available with a black background.
Warranty information needs to feature on the flyer.
Recycled content information needs to feature on the flyer.

Target Market(s)

Landscape Architects

Font styles to use
Serif

Requirements
Must have
• Professional fonts and graphics.
Should not have
• comic sans or similar fonts - cheap graphics

```html
<!DOCTYPE html>
<html lang="en">
<head>
<meta charset="utf-8">
<title>Halden Civic – Product Flyer</title>
<link href="https://fonts.googleapis.com/css2?family=Merriweather:wght@700;900&family=Lato:wght@400;700&display=swap" rel="stylesheet">
<style>
  :root {
    --brand-blue: #1174bc;
    --band-green: #4a9300;
    --headline-lime: #c8ef4e;
    --white: #ffffff;
    --ink-grey: #4d4d4f;
    --cream: #fbf3de;
    --badge-gold: #e9b93a;
    --badge-rim: #f6d978;
    --photo-dark: #2f4a1c;
    --photo-mid: #55792f;
    --photo-light: #7da04a;
  }
  * { margin: 0; padding: 0; box-sizing: border-box; }
  html, body { width: 848px; height: 1200px; overflow: hidden; background: var(--white); }
  .flyer { position: relative; width: 848px; height: 1200px; overflow: hidden; font-family: 'Lato', sans-serif; }

  .park-photo {
    position: absolute; left: 0; top: 0; width: 848px; height: 720px;
    background: linear-gradient(180deg, var(--photo-mid) 0%, var(--photo-dark) 30%, var(--photo-mid) 55%, var(--photo-light) 75%, var(--photo-mid) 100%);
  }
  .shapes { position: absolute; left: 0; top: 0; width: 848px; height: 1200px; }

  .brand-name {
    position: absolute; right: 30px; top: 46px;
    font-family: 'Lato', sans-serif; font-weight: 700; color: var(--ink-grey);
    font-size: 30px; line-height: 1; white-space: nowrap;
  }

  .headline {
    position: absolute; left: 47px; top: 62px; white-space: nowrap;
    font-family: 'Merriweather', serif; font-weight: 900; color: var(--white);
    font-size: 30px; line-height: 45px;
    text-shadow: 0 1px 3px rgba(0,0,0,.45);
  }
  .headline .lead { color: var(--headline-lime); }

  .recycle-band {
    position: absolute; left: 0; top: 279px; width: 848px; height: 87px;
    background: rgba(40, 48, 35, 0.55);
  }
  .recycle-icon {
    position: absolute; left: 16px; top: 268px; width: 120px; height: 116px;
    border-radius: 50%;
    background: radial-gradient(circle, #8fe22a 0%, #5fb51c 60%, #3f8c12 100%);
  }
  .recycle-copy {
    position: absolute; left: 152px; top: 293px; white-space: nowrap;
    color: var(--white); font-weight: 700; font-size: 21.5px; line-height: 28px;
  }

  .product-shot {
    position: absolute;
    background: linear-gradient(160deg, #6d5a49 0%, #3f3328 55%, #d9d2c4 100%);
  }
  .product-shot.table-hero { left: 418px; top: 400px; width: 430px; height: 270px; clip-path: polygon(4% 0, 98% 0, 100% 100%, 30% 95%, 0 35%); }
  .product-shot.bench-set { left: 86px; top: 444px; width: 168px; height: 130px; }
  .product-shot.armrest-seat { left: 348px; top: 456px; width: 122px; height: 160px; background: linear-gradient(160deg, #c0652a, #8a4418 60%, #6d6a64); }

  .feature-list {
    position: absolute; left: 66px; top: 673px; width: 760px; list-style: none;
    color: var(--white); font-size: 23px; line-height: 40px;
  }
  .feature-list li::before { content: "• "; }
  .feature-list .wrap { display: block; margin-left: -1px; }

  .range-band {
    position: absolute; left: 0; top: 938px; width: 848px; height: 94px;
    background: var(--band-green);
    display: flex; align-items: center; justify-content: center; text-align: center;
    font-family: 'Merriweather', serif; font-weight: 700; color: var(--white);
    font-size: 19.5px; line-height: 24px;
  }

  .warranty-badge {
    position: absolute; left: 72px; top: 1058px; width: 104px; height: 100px; border-radius: 50%;
    background: radial-gradient(circle, var(--badge-rim) 0%, var(--badge-gold) 70%, #c8921d 100%);
  }
  .warranty-copy {
    position: absolute; left: 200px; top: 1069px; white-space: nowrap;
    color: var(--cream); font-weight: 700; font-size: 19px; line-height: 24px; text-transform: uppercase;
  }
</style>
</head>
<body>
<main class="flyer">
  <div class="park-photo" role="img" aria-label="Park scene with green lawn, trees, a pond with reeds and a footpath"></div>

  <svg class="shapes" width="848" height="1200" viewBox="0 0 848 1200" aria-hidden="true">
    <polygon points="312,0 848,0 848,222" fill="var(--brand-blue)"/>
    <polygon points="336,0 848,0 848,190" fill="var(--white)"/>
    <polygon points="0,516 225,566 449,624 848,684 848,716 449,642 225,580 0,524" fill="var(--white)"/>
    <polygon points="0,524 225,580 449,642 848,716 848,1200 0,1200" fill="var(--brand-blue)"/>
    <polygon points="162,383 289,510 162,637 35,510" fill="var(--white)"/>
    <polygon points="410,410 537,537 410,664 283,537" fill="var(--white)"/>
  </svg>

  <div class="product-shot table-hero" role="img" aria-label="Picnic table and benches with dark composite battens on a cream aluminium frame"></div>
  <div class="product-shot bench-set" role="img" aria-label="Table and bench set with dark grey battens"></div>
  <div class="product-shot armrest-seat" role="img" aria-label="Seat with armrests and warm timber-tone battens"></div>

  <div class="brand-name">Halden Civic</div>

  <h1 class="headline">
    <span class="lead">EUROPEAN INSPIRED</span><br>
    with a unique and original design,<br>
    that is functional all while respecting<br>
    the environment.
  </h1>

  <div class="recycle-band"></div>
  <div class="recycle-icon" role="img" aria-label="Green recycling symbol"></div>
  <p class="recycle-copy">Featuring 98% recycled composite battens in a range of stain and<br>fade-resistant colour options and a unique aluminium frame design.</p>

  <ul class="feature-list">
    <li>Designed to make life easier for people.</li>
    <li>Created using extremely durable, ultra low maintenance materials.</li>
    <li>Site-specific for healthcare applications offering wheelchair<span class="wrap">accessibility options.</span></li>
    <li>Uniform length of 1800mm with tailored options available.</li>
    <li>Bolt down or freestanding options.</li>
  </ul>

  <p class="range-band">The Halden Civic range comprises of a seat with optional armrests,<br>bench seat and table, available in both standard or DDA designs.</p>

  <div class="warranty-badge" role="img" aria-label="Ten-year warranty seal"></div>
  <p class="warranty-copy">The capped composite battens come with a 10-year<br>commercial warranty covering staining, fading<br>and structural performance.</p>
</main>
</body>
</html>
```